Modernize Website: marcusfellwright.net

I am a novelist with an older-generation website at: marcusfellwright.net.

I am hoping to refresh this outdated website with a new, responsive redesign. I would prefer to host the code myself, and edit using Adobe Dreamweaver. So I’m not looking to use a hosted site builder like Plexo. Nor am I looking to use a CMS like Pagecraft.

In order to simplify the old site, there are a number of sections I’ll be looking to remove during this redesign. These are shown in the "MF Site Redesign" attachment. I can also provide imagery for new content (another book series in addition to the existing one), as well as higher-resolution imagery (if needed) of the old content.

Happy to answer any further questions.
Updates

I've uploaded a ZIP file containing high-res artwork associated with the new trilogy of books.

Target Market(s)

Readers of epic fantasy novels such as H.W.B. Castellane's THE WARDEN OF THE VALES, Harold P.Q. Ventris's A CROWN OF ASH AND RAIN, Victor Halloway's THE GATE OF STARS, or Dennis Vale's BLADE OF MERIVANE.

Industry/Entity Type

Entertainment

Coding

Coded - Design and coding required

Number of Pages Required

5+ page

Font styles to use
Serif
Decorative

Colors

Designer to choose colors to be used in the design.

Requirements
Must have
• I'm looking for a responsive design that displays nicely on both mobile and desktop devices. Existing site contains multiple pages, but these can obviously be combined into fewer pages (or even one) by divisions such as tabs, sections, and/or modal windows. See marcusfellwright.net for current content and "MF Site Redesign" attachment for content to be removed at this time.
Nice to have
• The ability to fulfill orders of autographed books directly from the website. I currently use Coinlo to do this, but it would be nice to incorporate a more comprehensive merchant service at a reasonable rate.
Should not have
• I'd like to host and control the site code myself. So please don't use a hosted web builder like Plexo, or a cloud-based CMS like Pagecraft.

```html
<!DOCTYPE html>
<html lang="en">
<head>
<meta charset="utf-8">
<title>Marcus Fellwright — Events</title>
<link href="https://fonts.googleapis.com/css2?family=Cinzel:wght@400;700&family=Crimson+Text:wght@400;600&family=Roboto:wght@400;500&display=swap" rel="stylesheet">
<style>
:root{
  --black:#000;
  --night:#0d0d13;
  --white:#fff;
  --red:#d0021b;
  --red-dark:#7a0010;
  --muted:#d8d8d8;
  --glow:rgba(200,0,20,.85);
}
*{box-sizing:border-box;margin:0;padding:0}
html,body{width:1200px;height:2163px;overflow:hidden;background:var(--night);color:var(--white)}
body{position:relative;font-family:'Roboto',Arial,sans-serif}

.site-header{position:absolute;left:0;top:0;width:1200px;height:121px;background:var(--black);z-index:5}
.brand{position:absolute;left:101px;top:38px;display:flex;align-items:center;gap:12px;font-family:'Cinzel',serif;font-weight:400;font-size:26px;color:var(--white);letter-spacing:1px}
.brand-dot{width:14px;height:14px;border-radius:50%;background:var(--red)}
.main-nav{position:absolute;left:529px;top:64px;display:flex;gap:0;font-size:16px;font-weight:500;text-transform:uppercase}
.main-nav span{margin-right:28px;display:flex;align-items:center;gap:4px}
.main-nav svg{width:10px;height:10px}
.login-btn{position:absolute;left:991px;top:57px;width:110px;height:35px;border-radius:18px;background:radial-gradient(ellipse at center,#ff1a30 0%,var(--red) 50%,var(--red-dark) 100%);display:flex;align-items:center;justify-content:center;gap:7px;font-size:15px;font-weight:500;box-shadow:0 0 10px rgba(208,2,27,.6)}

.dropdown{position:absolute;left:697px;top:121px;width:155px;height:195px;background:var(--black);z-index:6;font-size:15px;font-weight:500}
.dropdown span{position:absolute;left:21px}
.dropdown .active{left:0;width:155px;top:77px;height:38px;padding-left:21px;line-height:38px;background:linear-gradient(180deg,#5a0008 0%,var(--red) 45%,#a00014 100%)}

.hero{position:absolute;left:0;top:121px;width:1200px;height:560px;background:
  radial-gradient(ellipse at 62% 35%,#b89a86 0%,#7a6270 25%,#3f2f3f 50%,transparent 75%),
  linear-gradient(180deg,#5a4550 0%,#4a3848 45%,#2b2230 75%,var(--night) 100%)}
.hero-title{position:absolute;left:110px;top:295px;font-family:'Cinzel',serif;font-weight:700;font-size:92px;letter-spacing:1px;color:var(--white);text-shadow:0 0 18px var(--glow),0 0 6px var(--glow);z-index:2}

.events{position:absolute;left:0;top:681px;width:1200px;height:1090px;background:
  radial-gradient(ellipse at 10% 20%,rgba(150,60,20,.25) 0%,transparent 40%),
  radial-gradient(ellipse at 50% 100%,rgba(120,40,10,.35) 0%,transparent 45%),
  var(--night)}
.section-title{position:absolute;left:0;width:1200px;top:72px;text-align:center;font-family:'Cinzel',serif;font-weight:400;font-size:62px}
.event-card{position:absolute;width:308px;height:349px;box-shadow:0 8px 22px rgba(0,0,0,.7)}
.event-art{height:239px}
.event-info{height:110px;background:rgba(18,16,20,.92);text-align:center;font-family:'Crimson Text',serif;padding-top:14px}
.event-card.featured .event-info{background:linear-gradient(180deg,#600008 0%,var(--red) 55%,#a10016 100%)}
.event-date{font-size:22px;font-weight:600;letter-spacing:.5px}
.event-place{font-size:15px;line-height:21px;margin-top:4px;color:var(--white)}

.site-footer{position:absolute;left:0;top:1771px;width:1200px;height:392px;background:var(--black);text-align:center}
.footer-brand{position:absolute;left:0;width:1200px;top:70px;display:flex;justify-content:center;align-items:center;gap:12px;font-family:'Cinzel',serif;font-size:26px}
.social{position:absolute;left:513px;top:169px;display:flex;gap:12px}
.social span{width:50px;height:50px;border-radius:50%;background:var(--white);color:var(--red);display:flex;align-items:center;justify-content:center;font-family:'Roboto',sans-serif;font-size:9px;font-weight:500}
.footer-links{position:absolute;left:0;width:1200px;top:259px;font-size:15px}
.footer-links i{font-style:normal;margin:0 18px}
.legal{position:absolute;left:0;width:1200px;top:304px;font-size:14px}
.legal i{font-style:normal;margin:0 13px}
</style>
</head>
<body>
<header class="site-header">
  <div class="brand"><span class="brand-dot"></span>Marcus Fellwright</div>
  <nav class="main-nav">
    <span>Home</span>
    <span>Novels<svg viewBox="0 0 10 10"><path d="M1 3l4 4 4-4" fill="none" stroke="#fff" stroke-width="1.4"/></svg></span>
    <span>World<svg viewBox="0 0 10 10"><path d="M1 3l4 4 4-4" fill="none" stroke="#fff" stroke-width="1.4"/></svg></span>
    <span>Author<svg viewBox="0 0 10 10"><path d="M1 3l4 4 4-4" fill="none" stroke="#fff" stroke-width="1.4"/></svg></span>
    <span>Contact</span>
  </nav>
  <div class="login-btn"><svg width="11" height="13" viewBox="0 0 11 13"><path d="M2.5 6V4a3 3 0 0 1 6 0v2" fill="none" stroke="#fff" stroke-width="1.6"/><rect x="0.5" y="6" width="10" height="7" rx="1" fill="#fff"/></svg>LOGIN</div>
</header>

<div class="dropdown">
  <span style="top:14px">Biography</span>
  <span style="top:45px">News</span>
  <span class="active">Events</span>
  <span style="top:135px">Interviews</span>
  <span style="top:166px">Q &amp; A</span>
</div>

<section class="hero" role="img" aria-label="Fantasy scene: a dragon in a stormy sky above a stone tower and a lone figure"></section>
<h1 class="hero-title">AUTHOR</h1>

<main class="events">
  <h2 class="section-title">EVENTS</h2>

  <article class="event-card" style="left:99px;top:209px">
    <div class="event-art" role="img" aria-label="Illustration of a sword fight before a throne" style="background:linear-gradient(160deg,#7a5a78 0%,#5a4860 50%,#6a7a90 100%)"></div>
    <div class="event-info"><div class="event-date">NOVEMBER 11-13, 2016</div><div class="event-place">Harbor Point Writers Conference<br>in Seaview, CA</div></div>
  </article>
  <article class="event-card featured" style="left:447px;top:209px">
    <div class="event-art" role="img" aria-label="Illustration of travellers beneath a great tree in a burning forest" style="background:linear-gradient(170deg,#c45a20 0%,#a33a12 50%,#5a1a08 100%)"></div>
    <div class="event-info"><div class="event-date">FEBRUARY 21, 2009</div><div class="event-place">Riverbend Young Writers in<br>Oakdale, CA.</div></div>
  </article>
  <article class="event-card" style="left:793px;top:209px">
    <div class="event-art" role="img" aria-label="Illustration of a fiery horned beast" style="background:linear-gradient(170deg,#5a6a60 0%,#8a3a1a 50%,#b0401a 100%)"></div>
    <div class="event-info"><div class="event-date">MARCH 8-10, 2013</div><div class="event-place">Nam libero tempore, cum soluta nobis<br>optio cumque nihil</div></div>
  </article>

  <article class="event-card" style="left:99px;top:607px">
    <div class="event-art" role="img" aria-label="Illustration of a dragon breathing fire" style="background:linear-gradient(160deg,#1a1216 0%,#6a4a58 50%,#2a1a14 100%)"></div>
    <div class="event-info"><div class="event-date">MAY 25-28, 2012</div><div class="event-place">Nam libero tempore, cum soluta nobis<br>optio cumque nihil</div></div>
  </article>
  <article class="event-card" style="left:447px;top:607px">
    <div class="event-art" role="img" aria-label="Illustration of a centaur warrior with a spear" style="background:linear-gradient(170deg,#4a4a3a 0%,#8a6a40 50%,#5a3a2a 100%)"></div>
    <div class="event-info"><div class="event-date">AUG 29 - SEP 1, 2008</div><div class="event-place">Nam libero tempore, cum soluta nobis<br>optio cumque nihil</div></div>
  </article>
  <article class="event-card" style="left:793px;top:607px">
    <div class="event-art" role="img" aria-label="Illustration of armoured warriors with shields" style="background:linear-gradient(170deg,#6a6a6a 0%,#3a3636 55%,#1e1a1a 100%)"></div>
    <div class="event-info"><div class="event-date">JUNE 21, 2008</div><div class="event-place">Nam libero tempore, cum soluta nobis<br>optio cumque nihil</div></div>
  </article>
</main>

<footer class="site-footer">
  <div class="footer-brand"><span class="brand-dot"></span>Marcus Fellwright</div>
  <div class="social">
    <span>Frendo</span>
    <span>Chirper</span>
    <span><svg width="24" height="18" viewBox="0 0 24 18"><rect x="1" y="1" width="22" height="16" rx="2" fill="none" stroke="#d0021b" stroke-width="2"/><path d="M1 2l11 8 11-8" fill="none" stroke="#d0021b" stroke-width="2"/></svg></span>
  </div>
  <div class="footer-links">Home<i>|</i>Novels<i>|</i>World<i>|</i>Author<i>|</i>Contact</div>
  <div class="legal">© Copyright 2018 Marcus Fellwright. All Rights Reserved<i>|</i>Terms of Use<i>|</i>Privacy Policy.</div>
</footer>
</body>
</html>
```